Kettlecove Climate Business Card Design

Design new, 2 sides, business cards for a residential and light commercial heating, air conditioning contractor.

Target Market(s)

Homeowners, small businesses

Industry/Entity Type

Business

Contact Information for Business Card

Dominic Westerhall
Phone - 862-415-2736
Email
Address - PO box 518
Brightwater NJ 07912
Website - www.HarborBreezeLLC.example

Requirements
Must have
• logo, company colors, standard size with no die cut, so I can use nova stamp

```html
<!DOCTYPE html>
<html lang="en">
<head>
<meta charset="utf-8">
<title>Kettlecove Climate Business Card</title>
<link href="https://fonts.googleapis.com/css2?family=Source+Sans+3:wght@400;600;700&display=swap" rel="stylesheet">
<style>
  :root {
    --maroon: #9b1f32;
    --orange: #f28a30;
    --ink: #555555;
    --paper: #ffffff;
    --backdrop: #e8e5e1;
  }
  html, body {
    margin: 0;
    padding: 0;
    width: 1200px;
    height: 987px;
    overflow: hidden;
    background: var(--backdrop);
    font-family: "Source Sans 3", Arial, sans-serif;
  }
  .canvas {
    position: relative;
    width: 1200px;
    height: 987px;
  }
  .card {
    position: absolute;
    left: 292px;
    width: 615px;
    height: 351px;
    box-shadow: 0 3px 10px rgba(0,0,0,0.25);
    overflow: hidden;
  }
  .card-front { top: 131px; background: var(--paper); }
  .card-back { top: 506px; background: var(--orange); }

  .brand-mark {
    position: absolute;
    right: 34px;
    top: 90px;
    display: flex;
    align-items: center;
    gap: 10px;
    color: var(--maroon);
    font-weight: 700;
    font-size: 32px;
    line-height: 1;
    white-space: nowrap;
  }
  .brand-dot {
    width: 18px;
    height: 18px;
    border-radius: 50%;
    background: var(--orange);
    flex: none;
  }
  .person-name {
    position: absolute;
    left: 34px;
    top: 164px;
    margin: 0;
    color: var(--maroon);
    font-weight: 700;
    font-size: 22px;
    line-height: 26px;
    letter-spacing: 0.3px;
  }
  .person-title {
    position: absolute;
    left: 34px;
    top: 190px;
    margin: 0;
    color: var(--orange);
    font-size: 17px;
    line-height: 20px;
  }
  .divider {
    position: absolute;
    left: 34px;
    top: 215px;
    width: 548px;
    height: 2px;
    background: var(--orange);
  }
  .contact-list {
    position: absolute;
    left: 34px;
    top: 230px;
    margin: 0;
    padding: 0;
    list-style: none;
    color: var(--ink);
    font-size: 16px;
  }
  .contact-list li {
    display: flex;
    align-items: center;
    gap: 8px;
    height: 22px;
    white-space: nowrap;
  }
  .contact-list svg { width: 14px; height: 14px; fill: var(--maroon); flex: none; }
  .address {
    position: absolute;
    right: 33px;
    top: 248px;
    margin: 0;
    text-align: right;
    color: var(--ink);
    font-size: 16px;
    font-style: normal;
    line-height: 23px;
    white-space: nowrap;
  }
  .address .web { letter-spacing: 0.4px; }
  .edge-band {
    position: absolute;
    left: 0;
    bottom: 0;
    width: 615px;
    height: 14px;
  }
  .back-name {
    position: absolute;
    inset: 0;
    display: flex;
    align-items: center;
    justify-content: center;
    gap: 14px;
    color: var(--maroon);
    font-weight: 700;
    font-size: 54px;
    white-space: nowrap;
  }
  .back-name .brand-dot {
    width: 26px;
    height: 26px;
    background: var(--maroon);
  }
</style>
</head>
<body>
<div class="canvas">
  <section class="card card-front">
    <div class="brand-mark"><span class="brand-dot"></span>Kettlecove Climate</div>
    <h1 class="person-name">DOMINIC WESTERHALL</h1>
    <p class="person-title">CEO/Founder</p>
    <div class="divider"></div>
    <ul class="contact-list">
      <li><svg viewBox="0 0 24 24" aria-hidden="true"><path d="M6.6 10.8a15.1 15.1 0 0 0 6.6 6.6l2.2-2.2a1 1 0 0 1 1-.25 11.4 11.4 0 0 0 3.6.57 1 1 0 0 1 1 1V20a1 1 0 0 1-1 1A17 17 0 0 1 3 4a1 1 0 0 1 1-1h3.5a1 1 0 0 1 1 1c0 1.25.2 2.45.57 3.57a1 1 0 0 1-.25 1z"/></svg>862 415 2736</li>
      <li><svg viewBox="0 0 24 24" aria-hidden="true"><path d="M7 1h10a2 2 0 0 1 2 2v18a2 2 0 0 1-2 2H7a2 2 0 0 1-2-2V3a2 2 0 0 1 2-2zm0 3v14h10V4zm5 15.5a1.2 1.2 0 1 0 0 2.4 1.2 1.2 0 0 0 0-2.4z"/></svg>862 415 2790</li>
      <li><svg viewBox="0 0 24 24" aria-hidden="true"><path d="M6 2h12v5H6zM3 8h18a2 2 0 0 1 2 2v7h-4v5H5v-5H1v-7a2 2 0 0 1 2-2zm4 8v4h10v-4z"/></svg>862 415 2741</li>
      <li><svg viewBox="0 0 24 24" aria-hidden="true"><path d="M2 5h20v14H2zm2 2v.5l8 5.5 8-5.5V7z"/></svg>name@kettlecoveclimate.example</li>
    </ul>
    <address class="address">
      PO box 518<br>
      Brightwater NJ 07912<br>
      <span class="web">www.KettlecoveClimateLLC.example</span>
    </address>
    <svg class="edge-band" viewBox="0 0 615 14" preserveAspectRatio="none" aria-hidden="true">
      <polygon points="0,0 402,0 398,14 0,14" fill="var(--maroon)"/>
      <polygon points="406,0 615,0 615,14 402,14" fill="var(--orange)"/>
    </svg>
  </section>

  <section class="card card-back">
    <div class="back-name"><span class="brand-dot"></span>Kettlecove Climate</div>
  </section>
</div>
</body>
</html>
```